brightwell - Property Management DL Card

I am after a savvy designer to cut through junk mail! so many real estate agents use flyers to promote themselves and their business and usually sales. We are a property management firm (residential) and we want to represent landlords that have existing investment properties and need a quality agent to represent them. Can you help?
DL size, will be printed and delivered to mailboxes. For a look at our website go to www.brightwellrs.com.au. Keep it simple and clutter free.
it is to be double sided - with one side to be simple and clear - just our website, logo and telephone number on the back.
attached is our logo and our telephone number is 1300 48 92 16
the above are 2 essential elements to be included + our email address: admin@brightwellrs.com.au
also attached are our transparent price list

Target Market(s)
property investors,
people that manage properties themselves
Industry/Entity Type
Property Management
- arial
Look and feel

```html
<!DOCTYPE html>
<html lang="en">
<head>
<meta charset="utf-8">
<title>brightwell – Property Management DL Card</title>
<link href="https://fonts.googleapis.com/css2?family=Open+Sans:wght@300;400;600&display=swap" rel="stylesheet">
<style>
  :root {
    --page-bg: #e4e4e4;
    --card-white: #ffffff;
    --band-light: #e6d9b8;
    --band-dark: #c9b487;
    --ink: #2a2626;
    --ink-soft: #3a3a3a;
    --logo-box: #231f20;
    --label-box: #231f20;
    --tick: #6b5532;
    --link: #5a3a1a;
    --phone: #555555;
    --sky: #2f6fc4;
    --stucco: #d9c48f;
    --brick: #9c4a34;
    --lawn: #4f7a34;
  }
  * { box-sizing: border-box; margin: 0; padding: 0; }
  html, body { width: 1200px; height: 1200px; overflow: hidden; }
  body {
    background: var(--page-bg);
    font-family: "Open Sans", Arial, sans-serif;
    position: relative;
  }
  .card { position: absolute; width: 1000px; height: 500px; overflow: hidden; }
  .card--front { left: 122px; top: 55px; background: var(--band-light); }
  .card--back { left: 121px; top: 635px; background: var(--card-white); }

  .photo { position: absolute; top: 0; height: 385px; }
  .photo--villa {
    left: 0; width: 500px;
    background: linear-gradient(to bottom, var(--sky) 0%, #5b8fd0 35%, var(--stucco) 55%, #c9ae72 80%, var(--lawn) 100%);
  }
  .photo--brick {
    left: 500px; width: 500px;
    background: linear-gradient(to bottom, #3a7acc 0%, #b9cce6 28%, #8f7f6b 45%, var(--brick) 62%, #7a3a2a 80%, var(--lawn) 100%);
  }
  .photo-frame {
    position: absolute; left: 23px; top: 17px; width: 954px; height: 350px;
    border: 1px solid rgba(255,255,255,0.35);
  }

  .brand-plate {
    position: absolute; left: 423px; top: 173px; width: 154px; height: 66px;
    background: rgba(20,20,20,0.72);
    display: flex; align-items: center; justify-content: center;
  }
  .brand-name {
    font-weight: 300; color: #ffffff; font-size: 30px; letter-spacing: 0.5px;
  }

  .band {
    position: absolute; left: 0; top: 385px; width: 1000px; height: 115px;
    background: radial-gradient(ellipse at 55% 40%, #efe4c8 0%, var(--band-light) 45%, var(--band-dark) 100%);
  }
  .band-label {
    position: absolute; left: 336px; top: 24px; width: 328px; height: 25px;
    background: var(--label-box); color: #ffffff;
    font-size: 18px; line-height: 25px; text-align: center;
  }
  .benefits {
    position: absolute; left: 42px; top: 57px; width: 920px;
    display: flex; justify-content: space-between; list-style: none;
  }
  .benefit {
    display: flex; align-items: center; gap: 4px;
    font-size: 18px; color: var(--ink-soft); white-space: nowrap;
  }
  .benefit svg { width: 22px; height: 22px; flex: none; }

  .back-content {
    position: absolute; left: 0; top: 174px; width: 1000px;
    display: flex; flex-direction: column; align-items: center;
  }
  .back-plate {
    width: 242px; height: 90px; background: var(--logo-box);
    display: flex; align-items: center; justify-content: center;
    margin-bottom: 14px;
  }
  .back-plate .brand-name { font-size: 36px; }
  .contact { text-align: center; font-size: 16px; letter-spacing: 0.8px; color: var(--ink); line-height: 23px; }
  .contact--web { color: var(--link); }
  .contact--phone { color: var(--phone); font-weight: 600; font-size: 18px; letter-spacing: 1px; margin-top: 1px; }
</style>
</head>
<body>
  <section class="card card--front">
    <div class="photo photo--villa" role="img" aria-label="Photo of a cream rendered two-storey villa with tiled roof and garden under blue sky"></div>
    <div class="photo photo--brick" role="img" aria-label="Photo of a red brick two-storey family home with lawn and shrubs under a cloudy blue sky"></div>
    <div class="photo-frame"></div>
    <div class="brand-plate"><span class="brand-name">brightwell</span></div>

    <div class="band">
      <div class="band-label">Property Management specialists</div>
      <ul class="benefits">
        <li class="benefit">
          <svg viewBox="0 0 22 22"><circle cx="10" cy="12" r="8" fill="none" stroke="var(--tick)" stroke-width="1.6"/><path d="M6 11.5l3.5 3.5L19 4" fill="none" stroke="var(--tick)" stroke-width="2"/></svg>
          No postage and Admin fees
        </li>
        <li class="benefit">
          <svg viewBox="0 0 22 22"><circle cx="10" cy="12" r="8" fill="none" stroke="var(--tick)" stroke-width="1.6"/><path d="M6 11.5l3.5 3.5L19 4" fill="none" stroke="var(--tick)" stroke-width="2"/></svg>
          No hidden Extras
        </li>
        <li class="benefit">
          <svg viewBox="0 0 22 22"><circle cx="10" cy="12" r="8" fill="none" stroke="var(--tick)" stroke-width="1.6"/><path d="M6 11.5l3.5 3.5L19 4" fill="none" stroke="var(--tick)" stroke-width="2"/></svg>
          Excellent Communication
        </li>
        <li class="benefit">
          <svg viewBox="0 0 22 22"><circle cx="10" cy="12" r="8" fill="none" stroke="var(--tick)" stroke-width="1.6"/><path d="M6 11.5l3.5 3.5L19 4" fill="none" stroke="var(--tick)" stroke-width="2"/></svg>
          Technology Focussed
        </li>
      </ul>
    </div>
  </section>

  <section class="card card--back">
    <div class="back-content">
      <div class="back-plate"><span class="brand-name">brightwell</span></div>
      <p class="contact">PO Box B362, Harbourview NSW, 2091</p>
      <p class="contact contact--web">www.brightwellrs.com.au</p>
      <p class="contact">admin@brightwellrs.com.au</p>
      <p class="contact contact--phone">1.300.48.92.16</p>
    </div>
  </section>
</body>
</html>
```